Harborlight Plans (03)

We're designing a website to sell Medicare Supplements. Attached is the script we want to say and general layout, but please use your best knowledge to make it better. This platform should be extremely user-friendly, but we want to make it look fun and approachable! Most Insurance/medicare websites are very boring, drab, simple but we want this one to be more personalized, fun and sexy (but again, still user-friendly since our target demographic is 65+).

This homepage should include a fun and inviting quiz, the script is in the attachment below. It should also include the blurbs about what medicare supplements plans are and why they should buy them. Feel free to play around with cool fonts and imagery, we want the site to be engaging!

Target Market(s)

seniors

Industry/Entity Type

Insurance

Number of Pages Required

1 page

Requirements
Must have
• Quiz, company name and tag line, script
Nice to have
• fun, engaging elements

```html
<!DOCTYPE html>
<html lang="en">
<head>
<meta charset="utf-8">
<title>Harborlight Plans – Medicare Supplement</title>
<link href="https://fonts.googleapis.com/css2?family=Poppins:wght@300;400;500;600;700&display=swap" rel="stylesheet">
<style>
  :root {
    --blue: #2c6595;
    --blue-dark: #1f4f7b;
    --blue-soft: #a9c8e4;
    --blue-pale: #dbe9f5;
    --red: #e1444b;
    --ink: #333840;
    --muted: #4a4f57;
    --band: #f6f6f7;
    --white: #ffffff;
  }
  * { box-sizing: border-box; margin: 0; padding: 0; }
  html, body { width: 1200px; height: 2417px; overflow: hidden; }
  body {
    position: relative;
    background: var(--white);
    font-family: "Poppins", sans-serif;
    color: var(--ink);
  }
  .abs { position: absolute; }

  /* header */
  .brand { left: 111px; top: 34px; display: flex; align-items: center; gap: 12px; z-index: 2; }
  .brand-dot { width: 56px; height: 56px; border-radius: 50%; background: var(--blue); }
  .brand-name { font-size: 30px; font-weight: 700; color: var(--blue); line-height: 1; }
  .nav { left: 589px; top: 38px; display: flex; gap: 28px; font-size: 16px; z-index: 2; }
  .nav a { color: #222; text-decoration: none; }
  .nav a.active { color: var(--blue); border-left: 3px solid var(--blue); border-radius: 50%; padding-left: 10px; margin-left: -13px; }

  /* hero */
  .hero-art { left: 560px; top: 92px; width: 612px; height: 431px; border-radius: 46% 42% 10px 10px;
    background: linear-gradient(160deg, var(--blue-pale), #c9dcee 55%, #f4f8fc); z-index: 0; }
  .hero-title { left: 111px; top: 176px; width: 560px; font-size: 24px; font-weight: 600; color: var(--blue); line-height: 36px; white-space: nowrap; z-index: 1; }
  .call-btn { left: 111px; top: 277px; width: 258px; height: 56px; border-radius: 28px; background: var(--blue);
    color: var(--white); font-size: 22px; font-weight: 500; display: flex; align-items: center; justify-content: center; text-decoration: none; }
  .hero-sub { left: 111px; top: 356px; font-size: 23px; font-weight: 500; color: var(--red); line-height: 32px; }
  .hero-copy { left: 111px; top: 411px; width: 411px; font-size: 13.5px; line-height: 21.5px; text-align: justify; color: var(--ink); }

  /* quiz */
  .quiz-art { left: 112px; top: 633px; width: 366px; height: 764px; border-radius: 40px;
    background: linear-gradient(180deg, #e9f1f9, var(--blue-soft) 45%, var(--blue) 100%); }
  .quiz-intro { left: 535px; top: 626px; width: 620px; }
  .quiz-intro .lead { font-size: 27px; font-weight: 500; color: var(--red); line-height: 40px; }
  .quiz-intro .big { font-size: 35px; font-weight: 700; color: var(--blue); line-height: 44px; text-transform: uppercase; }
  .quiz-label { left: 535px; top: 816px; font-size: 30px; font-weight: 600; color: var(--blue); }
  .question { left: 535px; width: 352px; height: 58px; border: 3px solid var(--blue); border-radius: 30px;
    display: flex; align-items: center; gap: 14px; padding-left: 3px; font-size: 21px; color: var(--blue-dark); }
  .question .num { width: 48px; height: 48px; border-radius: 50%; background: var(--blue); color: var(--white);
    display: flex; align-items: center; justify-content: center; font-size: 20px; }
  .answers { left: 544px; list-style: none; font-size: 18px; color: #222; line-height: 33px; }

  /* info band */
  .band { left: 0; top: 1456px; width: 1200px; height: 878px; background: var(--band); }
  .info h2 { font-size: 19px; font-weight: 600; color: var(--red); margin-bottom: 6px; }
  .info p { font-size: 13.5px; line-height: 22.4px; color: var(--muted); text-align: justify; }
  .info ul { list-style: none; margin-top: 10px; font-size: 13.5px; line-height: 22.4px; color: var(--muted); }
  .info li { padding-left: 12px; position: relative; }
  .info li::before { content: ""; position: absolute; left: 0; top: 9px; width: 5px; height: 5px; border-radius: 50%; background: var(--red); }
  .info-what { left: 111px; top: 1520px; width: 552px; }
  .info-what ul { width: 520px; }
  .info-cost { left: 535px; top: 1868px; width: 553px; }
  .info-cost .note { margin-top: 12px; }
  .art-team { left: 703px; top: 1542px; width: 385px; height: 249px; border-radius: 24px;
    background: linear-gradient(135deg, #e7f1fb, #9fd0f2 50%, #2f7fc8); }
  .art-office { left: 56px; top: 1908px; width: 436px; height: 309px; border-radius: 24px;
    background: linear-gradient(45deg, #f0f3f7, #b6dbf5 50%, #3a96dc); }

  /* footer */
  .footer { left: 0; top: 2372px; width: 1200px; text-align: center; font-size: 15px; color: #333; }
</style>
</head>
<body>

<header>
  <div class="abs brand">
    <span class="brand-dot"></span>
    <span class="brand-name">Harborlight Plans</span>
  </div>
  <nav class="abs nav">
    <a class="active" href="#">Home</a>
    <a href="#">About</a>
    <a href="#">Quiz</a>
    <a href="#">Contact</a>
  </nav>
</header>

<section class="hero">
  <div class="abs hero-art" role="img" aria-label="Illustration of a mother holding her child beside a large checklist clipboard and a smiling doctor with a stethoscope"></div>
  <h1 class="abs hero-title">Be confident in choosing the Medicare<br>Supplement plan that’s right for you.</h1>
  <a class="abs call-btn" href="#">Call (800) 555-0142</a>
  <p class="abs hero-sub">to talk to a live agent.</p>
  <p class="abs hero-copy">We know insurance can be confusing. With so much information and not enough answers, we’re here to help you find the plan that works best for you, your family and your health.</p>
</section>

<section class="quiz">
  <div class="abs quiz-art" role="img" aria-label="Illustration of a doctor in a light blue coat holding a clipboard and a pointer"></div>
  <div class="abs quiz-intro">
    <p class="lead">Take this short quiz to</p>
    <p class="big">Find flexible and affordable plans that</p>
    <p class="lead">you can feel confident in.</p>
  </div>
  <h2 class="abs quiz-label">Quiz Script:</h2>

  <div class="abs question" style="top:877px"><span class="num">01</span>I am</div>
  <ol class="abs answers" style="top:939px">
    <li>a. Over 64 years old</li>
    <li>b. 64 years old</li>
    <li>c. Under 64 years old</li>
  </ol>

  <div class="abs question" style="top:1057px"><span class="num">02</span>I am</div>
  <ol class="abs answers" style="top:1119px">
    <li>a. Male</li>
    <li>b. Female</li>
    <li>c. Unspecified</li>
  </ol>

  <div class="abs question" style="top:1237px"><span class="num">03</span>I want to see</div>
  <ol class="abs answers" style="top:1300px">
    <li>a. Free plans</li>
    <li>b. Premium plans</li>
    <li>c. All plans</li>
  </ol>
</section>

<section>
  <div class="abs band"></div>

  <article class="abs info info-what">
    <h2>What is a Medicare Supplement plan?</h2>
    <p>Each Medicare Supplement insurance plan offers a different level of basic benefits, but each lettered plan will include the same standardized basic benefits regardless of insurance company and location. Medicare Supplement insurance plans do not always cover vision, dental, long-term care, or hearing aids, but all plans must cover at least a portion of the following basic benefits:</p>
    <ul>
      <li>Medicare Part A coinsurance costs up to an additional 365 days after Medicare benefits are exhausted</li>
      <li>Medicare Part A hospice care coinsurance or copayments</li>
      <li>Medicare Part B coinsurance or copayments</li>
      <li>First three pints of blood used in a medical procedure</li>
    </ul>
  </article>
  <div class="abs art-team" role="img" aria-label="Illustration of medical staff walking in front of a large health app screen with charts"></div>

  <div class="abs art-office" role="img" aria-label="Illustration of a medical team presenting charts in an office beside a large microscope"></div>
  <article class="abs info info-cost">
    <h2>Medicare Supplement insurance plan costs</h2>
    <p>Although private insurance companies are required to offer the same basic benefits for each lettered plan, they do have the ability to charge different premiums. You might want to shop around to find a Medicare Supplement insurance plan that may fit your medical and financial needs. Insurance companies may price their plan premiums in any of the following ways:</p>
    <ul>
      <li>Community no-age-rated: These Medicare Supplement insurance plans charge premiums that are the same across the board, regardless of age.</li>
      <li>Issue-age-rated: These plans base their premiums on your age when you first enrolled in the policy. Therefore, the younger you are when you enroll in this type of plan, the lower your premium will be.</li>
      <li>Attained-age-rated: Like issue-age-rated, these plans base their premiums on the age you were when you first bought a policy, but unlike issue-age-rated, premiums increase as you get older.</li>
    </ul>
    <p class="note">Please note that no matter what rating method an insurance company uses, premiums may increase over time for reasons other than age, such as inflation.</p>
  </article>
</section>

<footer class="abs footer">Copyrights @ 2020 Harborlight Plans. All Rights Reserved.</footer>

</body>
</html>
```